Velk Partners Building Business Cards

We need a business card that reflects our business as "Solar Experts" in San Diego. Browse our website www.velkpartners.example our License needs to be displayed as "CSLB# 3867140" our phone number is (619) 555-0187

Save thousands on your electric bills and increase the value of your home while helping to protect the environment. Our solar installation experts will help you design the system that's right for you, using only the highest quality equipment that will look great and give you ideal performance. Our goal is to make you energy independent, and get your electric bill to 0.

Paul Osterby
(619) 555-0187
paul@velkpartners.example

Target Market(s)

Home owners in san diego looking for solar

Industry/Entity Type

Solar Energy

Contact Information for Business Card

Paul Osterby
(619) 555-0187
paul@velkpartners.example

Font styles to use
Other font styles liked:
• Use our logo font

Requirements
Must have
• License needs to be displayed as "CSLB# 3867140" our phone number is (619) 555-0187
Nice to have
• Real images of rooftop home solar in san diego
Should not have
• our business address

```html
<!DOCTYPE html>
<html lang="en">
<head>
<meta charset="utf-8">
<title>Velk Partners Building – Business Cards</title>
<link rel="stylesheet" href="https://fonts.googleapis.com/css2?family=Open+Sans:wght@400;600;700&display=swap">
<style>
  :root {
    --page-bg: #3a322e;
    --card-bg: #0c0c0c;
    --card-edge: #1c1c1c;
    --gold: #f3ad00;
    --white: #f2f2f2;
    --silver: #c9c9c9;
  }
  * { box-sizing: border-box; margin: 0; padding: 0; }
  html, body {
    width: 1200px; height: 900px; overflow: hidden;
    background: var(--page-bg);
    font-family: "Open Sans", Arial, sans-serif;
  }
  .stage {
    position: relative; width: 1200px; height: 900px;
    display: flex; align-items: center; justify-content: center; gap: 50px;
  }
  .card {
    width: 525px; height: 300px;
    background: var(--card-bg);
    border: 1px solid var(--card-edge);
    box-shadow: 0 12px 30px rgba(0,0,0,.45);
    position: relative;
  }
  /* Front */
  .card-front { display: flex; align-items: center; }
  .brand-mark {
    width: 230px; height: 100%;
    display: flex; align-items: center; justify-content: center; gap: 12px;
    padding-left: 20px;
  }
  .brand-dot {
    width: 22px; height: 22px; border-radius: 50%;
    background: var(--gold); flex: none;
  }
  .brand-name {
    color: var(--white); font-weight: 600; font-size: 19px; line-height: 1.2;
  }
  .divider {
    width: 1px; height: 150px;
    background: linear-gradient(to bottom, transparent, var(--gold), transparent);
  }
  .contact { padding-left: 26px; color: var(--white); }
  .contact-name {
    color: var(--gold); font-weight: 700; font-size: 17px; margin-bottom: 18px;
  }
  .contact-license { font-size: 14px; margin-bottom: 10px; }
  .contact-license strong { font-weight: 700; }
  .contact-line {
    display: flex; align-items: center; gap: 10px;
    font-size: 13.5px; margin-bottom: 4px;
  }
  .contact-line svg { width: 11px; height: 11px; flex: none; }
  /* Back */
  .card-back {
    display: flex; align-items: center; justify-content: center;
  }
  .back-name {
    color: var(--silver); font-weight: 700; font-size: 34px; letter-spacing: .5px;
  }
</style>
</head>
<body>
<main class="stage">
  <section class="card card-front" aria-label="Business card front">
    <div class="brand-mark">
      <span class="brand-dot"></span>
      <span class="brand-name">Velk Partners<br>Building</span>
    </div>
    <div class="divider"></div>
    <div class="contact">
      <p class="contact-name">Paul Osterby</p>
      <p class="contact-license"><strong>License:</strong> CSLB# 3867140</p>
      <p class="contact-line">
        <svg viewBox="0 0 12 12" aria-hidden="true"><path fill="#f3ad00" d="M2.3 0.6l1.8 2.3-1 1.2c.6 1.5 1.9 2.8 3.4 3.4l1.2-1 2.3 1.8-1 2c-4.3.1-8.2-3.8-8.1-8.1z"/></svg>
        (619) 555-0187
      </p>
      <p class="contact-line">
        <svg viewBox="0 0 12 12" aria-hidden="true"><rect x="0.5" y="2" width="11" height="8" fill="#f3ad00"/><path d="M0.5 2l5.5 4.5 5.5-4.5" fill="none" stroke="#0c0c0c" stroke-width="1"/></svg>
        paul@velkpartners.example
      </p>
    </div>
  </section>
  <section class="card card-back" aria-label="Business card back">
    <p class="back-name">Velk Partners Building</p>
  </section>
</main>
</body>
</html>
```